Harborline Auto LLC

Car Dealer Customer Service
Address: 2874 Cresthaven Road, Shelbyville, TN 37162
web: www.harborlineautoxq.net
email: harborlineautoxq@mailnest.example
Phone: (931) 555-0148
Phone: (629) 555-0173

```html
<!DOCTYPE html>
<html lang="en">
<head>
<meta charset="utf-8">
<title>Harborline Auto – Business Cards</title>
<link rel="stylesheet" href="https://fonts.googleapis.com/css2?family=Montserrat:wght@400;500;700;800&display=swap">
<style>
  :root {
    --backdrop: #d6d6d6;
    --paper: #f1f1ef;
    --brand-blue: #1877b8;
    --accent-yellow: #eeb23a;
    --body-grey: #6b6b6b;
    --edge-blue: #1a86c4;
  }
  * { margin: 0; padding: 0; box-sizing: border-box; }
  html, body {
    width: 1200px; height: 1051px; overflow: hidden;
    background: var(--backdrop);
    font-family: "Montserrat", sans-serif;
  }
  .stage { position: relative; width: 1200px; height: 1051px; }
  .card {
    position: absolute;
    width: 500px; height: 286px;
    background: var(--paper);
    border-bottom: 5px solid var(--edge-blue);
    box-shadow: 0 18px 40px rgba(0,0,0,0.18);
  }
  .card--contact { left: 80px; top: 470px; }
  .card--brand { left: 620px; top: 300px; }

  .contact-block { position: absolute; left: 34px; top: 34px; }
  .contact-title {
    font-weight: 700; font-size: 14px; color: var(--brand-blue);
    margin-bottom: 4px;
  }
  .contact-address { font-size: 12.5px; line-height: 1.45; color: var(--body-grey); margin-bottom: 10px; }
  .contact-list { list-style: none; }
  .contact-list li {
    display: flex; align-items: center; gap: 8px;
    font-size: 12.5px; line-height: 1.5; color: var(--body-grey);
  }
  .contact-list svg { width: 11px; height: 11px; fill: var(--accent-yellow); flex: none; }

  .wordmark {
    position: absolute; display: flex; align-items: center; gap: 10px;
    font-weight: 800; color: var(--brand-blue); letter-spacing: 0.5px;
    text-transform: uppercase;
  }
  .wordmark__dot { border-radius: 50%; background: var(--brand-blue); flex: none; }
  .card--contact .wordmark { right: 34px; bottom: 36px; font-size: 22px; }
  .card--contact .wordmark__dot { width: 20px; height: 20px; }
  .card--brand .wordmark { left: 50%; top: 50%; transform: translate(-50%, -50%); font-size: 30px; }
  .card--brand .wordmark__dot { width: 26px; height: 26px; }
</style>
</head>
<body>
<main class="stage">
  <section class="card card--contact" aria-label="Business card back">
    <div class="contact-block">
      <p class="contact-title">Car Dealer Customer Service</p>
      <p class="contact-address">2874 Cresthaven Road<br>Shelbyville, TN 37162</p>
      <ul class="contact-list">
        <li><svg viewBox="0 0 24 24" aria-hidden="true"><path d="M6.6 10.8a15.1 15.1 0 0 0 6.6 6.6l2.2-2.2a1 1 0 0 1 1-.25 11.4 11.4 0 0 0 3.6.57 1 1 0 0 1 1 1V20a1 1 0 0 1-1 1A17 17 0 0 1 3 4a1 1 0 0 1 1-1h3.5a1 1 0 0 1 1 1c0 1.25.2 2.45.57 3.57a1 1 0 0 1-.25 1z"/></svg>(931) 555-0148</li>
        <li><svg viewBox="0 0 24 24" aria-hidden="true"><path d="M6.6 10.8a15.1 15.1 0 0 0 6.6 6.6l2.2-2.2a1 1 0 0 1 1-.25 11.4 11.4 0 0 0 3.6.57 1 1 0 0 1 1 1V20a1 1 0 0 1-1 1A17 17 0 0 1 3 4a1 1 0 0 1 1-1h3.5a1 1 0 0 1 1 1c0 1.25.2 2.45.57 3.57a1 1 0 0 1-.25 1z"/></svg>(629) 555-0173</li>
        <li><svg viewBox="0 0 24 24" aria-hidden="true"><path d="M2 5h20v14H2z M2 5l10 8 10-8" /></svg>harborlineautoxq@mailnest.example</li>
        <li><svg viewBox="0 0 24 24" aria-hidden="true"><circle cx="12" cy="12" r="10"/></svg>www.harborlineautoxq.net</li>
      </ul>
    </div>
    <div class="wordmark"><span class="wordmark__dot"></span>Harborline Auto</div>
  </section>

  <section class="card card--brand" aria-label="Business card front">
    <div class="wordmark"><span class="wordmark__dot"></span>Harborline Auto</div>
  </section>
</main>
</body>
</html>
```